Commercial Post Cards

We are looking for 3 postcards that are similar but target 3 commercial property types. they will be 6x9 cards can be front and back or not.
1. Hotel Postcard – Taviqon / Bed Bug Protection
Use the attached Taviqon sample as the primary direction.
The focus should be:
Proactive bed bug prevention and control
Protecting guests and the hotel's reputation
Regular inspections
Documentation and risk management
Professional commercial pest management
The backside should transition into our General Pest Control services, showing that we can be the hotel's complete pest management provider beyond just bed bugs.
2. Apartment Complex Postcard
Target apartment owners, property managers, and management companies.
Focus on:
General pest control
Bed bug control
Rodent control
Preventative pest management
Protecting residents and the property
Reliable, ongoing service and documentation
The message should position us as a full-service pest management partner for multifamily properties.

3. Commercial Building Postcard
Target office buildings, banks, storage facilities, and other commercial properties.

Focus on:
General commercial pest control
Rodent control
Fly management
Recurring service programs
Protecting the property, employees, customers, and reputation

Overall Direction
All three postcards should have a consistent brand and visual style, but each should feel specifically designed for its target market.

We want the messaging to communicate:
Professional • Reliable • Proactive • Locally Owned & Operated • Serving Since 2017

The goal is not to overwhelm the reader with information. These should be marketing pieces that quickly communicate the problem we solve, our expertise, and why a commercial property should contact us.

I have included some of our marketing materials for help with what we do.

```html
<!DOCTYPE html>
<html lang="en">
<head>
<meta charset="utf-8">
<title>SiteShield Commercial Postcard – Ridgeline Pest Control</title>
<link rel="stylesheet" href="https://fonts.googleapis.com/css2?family=Oswald:wght@400;500;600;700&display=swap">
<style>
  :root{
    --ink:#0e0e0e;
    --ink-bar:#161616;
    --orange:#f05a22;
    --white:#ffffff;
    --paper:#f4f4f4;
    --stage:#e3e3e3;
    --rule:#bdbdbd;
  }
  *{box-sizing:border-box;margin:0;padding:0}
  html,body{width:1200px;height:598px;overflow:hidden}
  body{background:var(--stage);font-family:'Oswald',sans-serif;color:var(--white);position:relative}
  .card{position:absolute;top:109px;width:570px;height:380px;background:var(--ink);overflow:hidden}
  .card--front{left:20px}
  .card--back{left:610px}

  .brand{position:absolute;left:20px;top:22px}
  .brand__name{display:flex;align-items:center;gap:8px;font-size:26px;font-weight:600;line-height:1;color:var(--white)}
  .brand__mark{width:18px;height:18px;background:var(--orange)}
  .brand__tagline{margin-top:6px;font-size:10px;font-weight:400;letter-spacing:.5px;color:var(--orange)}

  /* front */
  .front__photo{position:absolute;right:0;top:0;width:340px;height:352px;
    background:linear-gradient(90deg,var(--ink) 0%,#1b2430 28%,#34465d 58%,#4f6784 80%,#6c85a3 100%)}
  .front__copy{position:absolute;left:20px;top:94px}
  .headline{font-size:56px;font-weight:700;line-height:1;letter-spacing:-.5px}
  .headline__accent{color:var(--orange)}
  .subhead{margin-top:8px;font-size:23px;font-weight:500;line-height:1.25}
  .promise{margin-top:6px;font-size:10px;line-height:1.45;color:var(--orange)}

  .services{position:absolute;left:0;top:252px;width:340px;height:64px}
  .services__shape{position:absolute;left:0;top:0}
  .services__grid{position:absolute;left:12px;top:7px;display:grid;grid-template-columns:92px 82px 110px;row-gap:6px}
  .service{display:flex;align-items:center;gap:6px;font-size:9.5px;font-weight:500;line-height:1.15;color:var(--ink)}
  .service__icon{flex:none;width:22px;height:22px;background:var(--orange);display:flex;align-items:center;justify-content:center}

  .footer{position:absolute;left:0;bottom:0;width:100%;height:28px;background:var(--ink-bar);
    display:flex;justify-content:center;align-items:center;gap:12px;font-size:12px;font-weight:500;color:var(--orange)}
  .footer__sep{width:1px;height:14px;background:var(--white)}

  /* back */
  .back__divider{position:absolute;left:307px;top:22px;width:1px;height:318px;background:var(--rule)}
  .back__stamp{position:absolute;right:32px;top:38px;width:78px;height:91px;border:1px solid var(--rule)}
  .back__address{position:absolute;left:326px;width:226px;height:1px;background:var(--rule)}
  .back__copy{position:absolute;left:15px;top:90px;width:288px}
  .back__title{font-size:19px;font-weight:600;line-height:1.25}
  .pests{margin-top:8px;display:flex;flex-wrap:wrap;row-gap:10px;font-size:9.5px;font-weight:400}
  .pest{display:flex;align-items:center;gap:4px;padding:0 6px;border-right:1px solid #777}
  .pest:first-child,.pest--row{padding-left:0}
  .pest:last-child,.pest--end{border-right:none}
  .pest__dot{width:8px;height:8px;border-radius:50%;background:var(--white)}
  .cta{position:absolute;left:0;top:204px;width:287px;height:70px;background:var(--paper);padding:6px 0 0 12px}
  .cta__main{font-size:30px;font-weight:700;line-height:1;color:var(--orange)}
  .cta__sub{margin-top:2px;font-size:21px;font-weight:600;line-height:1.15;color:var(--ink)}
  .contact{position:absolute;left:18px;top:287px;display:grid;grid-template-columns:130px 150px;row-gap:12px;column-gap:14px;font-size:10.5px;font-weight:500}
  .contact__item{display:flex;align-items:center;gap:6px;white-space:nowrap}
  .contact__icon{width:16px;height:16px;flex:none}
</style>
</head>
<body>

<!-- Front -->
<section class="card card--front">
  <div class="front__photo" role="img" aria-label="Modern glass commercial office building lit at dusk"></div>

  <div class="brand">
    <div class="brand__name"><span class="brand__mark"></span>Ridgeline Pest Control</div>
    <div class="brand__tagline">COMMERCIAL PEST MANAGEMENT SPECIALISTS</div>
  </div>

  <div class="front__copy">
    <h1 class="headline"><span class="headline__accent">SITE</span>SHIELD</h1>
    <p class="subhead">PROTECT YOUR BUSINESS<br>PROTECT YOUR BRAND</p>
    <p class="promise">RELIABLE COMMERCIAL PEST CONTROL<br>YOU CAN COUNT ON.</p>
  </div>

  <div class="services">
    <svg class="services__shape" width="340" height="64" viewBox="0 0 340 64"><polygon points="0,0 340,0 294,64 0,64" fill="#ffffff"/></svg>
    <div class="services__grid">
      <div class="service"><span class="service__icon"><svg width="12" height="12" viewBox="0 0 12 12"><circle cx="6" cy="6" r="3" fill="#fff"/></svg></span>GENERAL PEST<br>CONTROL</div>
      <div class="service"><span class="service__icon"><svg width="12" height="12" viewBox="0 0 12 12"><ellipse cx="6" cy="6.5" rx="3" ry="4" fill="#fff"/></svg></span>BED BUG<br>CONTROL</div>
      <div class="service"><span class="service__icon"><svg width="14" height="14" viewBox="0 0 14 14"><path d="M7 1.5 12 3.5V7c0 3-2.3 4.8-5 5.6C4.3 11.8 2 10 2 7V3.5Z" fill="none" stroke="#fff" stroke-width="1.3"/><path d="M4.6 7.1 6.3 8.7 9.4 5.4" fill="none" stroke="#fff" stroke-width="1.3"/></svg></span>PREVENTATIVE<br>PROGRAMS</div>
      <div class="service"><span class="service__icon"><svg width="12" height="14" viewBox="0 0 12 14"><rect x="1.5" y="1.5" width="9" height="11" fill="none" stroke="#fff" stroke-width="1.2"/><path d="M3.5 5h5M3.5 7.5h5M3.5 10h5" stroke="#fff" stroke-width="1"/></svg></span>DOCUMENTED<br>SERVICE</div>
      <div class="service"><span class="service__icon"><svg width="14" height="10" viewBox="0 0 14 10"><ellipse cx="7" cy="6" rx="5" ry="3.3" fill="#fff"/></svg></span>RODENT<br>CONTROL</div>
    </div>
  </div>

  <footer class="footer">
    <span>PROFESSIONAL. RELIABLE. PROACTIVE.</span><span class="footer__sep"></span>
    <span>SERVING SINCE 2017</span><span class="footer__sep"></span>
    <span>LOCALLY OWNED &amp; OPERATED</span>
  </footer>
</section>

<!-- Back -->
<section class="card card--back">
  <div class="brand">
    <div class="brand__name"><span class="brand__mark"></span>Ridgeline Pest Control</div>
    <div class="brand__tagline">COMMERCIAL PEST MANAGEMENT SPECIALISTS</div>
  </div>

  <div class="back__divider"></div>
  <div class="back__stamp"></div>
  <div class="back__address" style="top:151px"></div>
  <div class="back__address" style="top:187px"></div>
  <div class="back__address" style="top:222px"></div>

  <div class="back__copy">
    <h2 class="back__title">COMPLETE PEST PROTECTION FOR<br>YOUR ENTIRE PROPERTY</h2>
    <div class="pests">
      <span class="pest"><span class="pest__dot"></span>SPIDERS</span>
      <span class="pest"><span class="pest__dot"></span>COCKROACHES</span>
      <span class="pest"><span class="pest__dot"></span>ANTS</span>
      <span class="pest pest--end"><span class="pest__dot"></span>SILVERFISH</span>
      <span class="pest pest--row"><span class="pest__dot"></span>PANTRY PESTS</span>
      <span class="pest"><span class="pest__dot"></span>RODENTS</span>
      <span class="pest"><span class="pest__dot"></span>FLIES</span>
      <span class="pest pest--end"><span class="pest__dot"></span>WASPS</span>
    </div>
  </div>

  <div class="cta">
    <div class="cta__main">CALL OR EMAIL</div>
    <div class="cta__sub">FOR A CUSTOM QUOTE TODAY!</div>
  </div>

  <div class="contact">
    <div class="contact__item"><svg class="contact__icon" viewBox="0 0 16 16"><circle cx="8" cy="8" r="7" fill="none" stroke="#f05a22" stroke-width="1.2"/><path d="M5.3 4.5l1.4-.3.8 1.8-.9.7c.4.9 1.1 1.6 2 2l.7-.9 1.8.8-.3 1.4c-2.9.2-5.7-2.6-5.5-5.5z" fill="#f05a22"/></svg>555-014-2210 (IDAHO)</div>
    <div class="contact__item"><svg class="contact__icon" viewBox="0 0 16 16"><circle cx="8" cy="8" r="7" fill="none" stroke="#f05a22" stroke-width="1.2"/><rect x="5.6" y="3.8" width="4.8" height="8.4" rx=".8" fill="none" stroke="#f05a22" stroke-width="1"/></svg>555-017-3390 (CELL)</div>
    <div class="contact__item"><svg class="contact__icon" viewBox="0 0 16 16"><circle cx="8" cy="8" r="7" fill="none" stroke="#f05a22" stroke-width="1.2"/><rect x="4.3" y="5.3" width="7.4" height="5.4" fill="none" stroke="#f05a22" stroke-width="1"/><path d="M4.3 5.3 8 8.4l3.7-3.1" fill="none" stroke="#f05a22" stroke-width="1"/></svg>office@ridgelinepest.com</div>
    <div class="contact__item"><svg class="contact__icon" viewBox="0 0 16 16"><circle cx="8" cy="8" r="7" fill="none" stroke="#f05a22" stroke-width="1.2"/><circle cx="8" cy="8" r="4" fill="none" stroke="#f05a22" stroke-width="1"/><path d="M4 8h8M8 4c-1.6 2.4-1.6 5.6 0 8M8 4c1.6 2.4 1.6 5.6 0 8" fill="none" stroke="#f05a22" stroke-width=".9"/></svg>www.ridgelinepest.com</div>
  </div>

  <footer class="footer">
    <span>PROFESSIONAL. RELIABLE. PROACTIVE.</span><span class="footer__sep"></span>
    <span>SERVING SINCE 2017</span><span class="footer__sep"></span>
    <span>LOCALLY OWNED &amp; OPERATED</span>
  </footer>
</section>

</body>
</html>
```